Website for a Psychologist in Private Practice

I need a cool web design for my website: www.drkalvoric.com. I would like it to look professional. Keep all the current content and add: Space for video; radio spots (see Silver Cedar Tunes Logo below for those); Quick Inquiry; Friendora link; 5 star rating on Rivo; a map; reviews from former patients. I am open to suggestions.

Target Market(s)

Those seeking individual and marital counseling.

Industry/Entity Type

Mental Health

Number of Pages Required

1 page

Font styles to use
Sans Serif
Other font styles liked:
• I'm open but no hard to read script

Requirements
Must have
• All the content on my home page with link for video and radio spots. List services and degrees and expertices (pics not necessary).
Nice to have
• A video of me and radio conversations (logo of Silver Cedar Tunes radio attached).
Should not have
• Cartoons, comedy, etc.... I don't need pictures of services (marital, depression, etc...) Just list those.

```html
<!DOCTYPE html>
<html lang="en">
<head>
<meta charset="utf-8">
<title>Dr. Mara Z. Kalvoric — Individual and Marital Counseling</title>
<link href="https://fonts.googleapis.com/css2?family=Cinzel:wght@400;600;700&family=Lato:ital,wght@0,400;0,700;0,900;1,400&display=swap" rel="stylesheet">
<style>
:root{
  --blue:#2a7fc1;
  --green:#108c12;
  --ink:#2b2b2b;
  --muted:#555;
  --black:#000;
  --review-bg:#e6e6e6;
  --footer-bg:#262626;
  --footer-deep:#151515;
  --form-bg:#ececec;
  --line:#d8d8d8;
}
*{box-sizing:border-box;margin:0;padding:0}
html,body{width:1200px;height:2922px;overflow:hidden}
body{font-family:"Lato",Arial,sans-serif;color:var(--ink);background:#fff;position:relative}
.wrap{width:1040px;margin:0 auto;position:relative;height:100%}

/* header */
.site-header{height:117px}
.brand{position:absolute;left:0;top:34px;font-family:"Cinzel",Georgia,serif;font-size:39px;font-weight:600;color:var(--blue);letter-spacing:.5px;white-space:nowrap}
.pill{position:absolute;top:39px;height:43px;border:1px solid var(--line);border-radius:22px;display:flex;align-items:center;gap:10px;padding:0 18px 0 24px;font-size:15px;color:var(--ink);white-space:nowrap}
.pill svg{width:20px;height:20px;flex:none}
.pill-email{left:489px;width:306px}
.pill-call{left:806px;width:234px}
.pill b{font-weight:400}

/* nav */
.main-nav{height:60px;background:var(--green)}
.main-nav ul{list-style:none;display:flex;height:60px;align-items:center;justify-content:space-between}
.main-nav li{position:relative;font-weight:700;font-size:18px;color:#fff;letter-spacing:.3px;white-space:nowrap}
.main-nav li.active{background:var(--blue);padding:8px 17px;border:1px solid #6fb0e0}
.main-nav li.sep{width:1px;height:34px;background:rgba(255,255,255,.25)}

/* hero */
.hero{height:487px;position:relative;background:linear-gradient(100deg,#e8e6e2 0%,#cfc6bc 30%,#b9b3ad 55%,#d7d9da 80%,#eceded 100%)}
.hero-caption{position:absolute;left:78px;top:189px;width:422px;height:107px;background:rgba(40,40,40,.78);padding:16px 22px}
.hero-caption h1{font-family:"Cinzel",Georgia,serif;font-weight:400;color:#fff;font-size:25px;line-height:30px;letter-spacing:.5px}
.btn-start{position:absolute;left:26px;top:84px;background:var(--blue);color:#fff;font-weight:700;font-size:19px;padding:4px 16px;border:1px solid #8cc3ea}
.arrow{position:absolute;top:215px;width:32px;height:32px;background:#2b2b2b;display:flex;align-items:center;justify-content:center}
.arrow.left{left:8px}.arrow.right{right:8px}

/* shared headings */
.section-title{font-family:"Cinzel",Georgia,serif;font-size:33px;font-weight:600;color:var(--blue);letter-spacing:.5px;white-space:nowrap;line-height:1.2}
.section-title em{font-style:normal;color:var(--green)}
.rule{width:60px;height:3px;background:var(--blue);margin-top:10px}

/* about */
.about{height:466px}
.about-main{position:absolute;left:0;top:72px;width:705px}
.about-text{margin-top:22px;font-size:13.5px;line-height:26px;color:var(--muted)}
.about-text a{color:var(--ink);font-weight:700;text-decoration:none}
.values{display:flex;margin-top:36px}
.value{display:flex;gap:16px;width:372px}
.value-icon{width:78px;height:78px;border:2px solid var(--blue);border-radius:50%;flex:none;display:flex;align-items:center;justify-content:center}
.value h3{font-family:"Cinzel",Georgia,serif;font-weight:400;color:var(--blue);font-size:20px;margin-top:4px}
.value p{font-size:13.5px;line-height:20px;color:var(--muted);margin-top:4px}
.inquiry{position:absolute;left:726px;top:78px;width:314px;height:333px;background:var(--form-bg);border-radius:5px;overflow:hidden}
.inquiry h2{background:var(--green);color:#fff;font-size:19px;font-weight:700;height:48px;line-height:48px;padding-left:24px;border-radius:5px 5px 0 0}
.inquiry form{padding:14px 24px 0}
.field{height:36px;background:#fff;border:1px solid var(--line);margin-bottom:9px;font-size:12.5px;color:#888;padding:10px 10px;position:relative}
.field.msg{height:68px}
.field .caret{position:absolute;right:10px;top:14px;width:0;height:0;border-left:5px solid transparent;border-right:5px solid transparent;border-top:6px solid #c79a2c}
.btn-submit{display:inline-block;background:var(--blue);color:#fff;font-weight:700;font-size:16px;padding:9px 18px;margin-top:8px;border-radius:2px}

/* expertise */
.expertise{height:540px;background:var(--black)}
.exp-col{position:absolute;left:25px;top:62px}
.checklist{list-style:none;margin-top:40px}
.checklist li{display:flex;align-items:center;gap:16px;color:#fff;font-weight:700;font-size:15px;height:38px}
.video-col{position:absolute;left:557px;top:62px}
.video{position:absolute;left:557px;top:154px;width:483px;height:317px;background:linear-gradient(120deg,#8c8c86 0%,#6d6a64 35%,#5a5a5c 60%,#858585 100%);display:flex;align-items:center;justify-content:center}

/* sessions */
.sessions{height:615px}
.sessions-head{position:absolute;left:0;top:58px}
.session-list{position:absolute;left:0;top:150px;width:540px;list-style:none}
.session-list li{display:flex;gap:14px;font-size:15px;line-height:21px;margin-bottom:26px;color:var(--ink)}
.session-list svg{flex:none;margin-top:2px}
.radio{position:absolute;left:557px;top:58px;width:483px}
.radio .section-title{font-size:31px;letter-spacing:0}
.radio-art{position:absolute;left:557px;top:134px;width:483px;height:428px;background:linear-gradient(160deg,#e8336f 0%,#d06a86 30%,#b68d7f 60%,#7c7a71 100%)}

/* review */
.review{height:298px;background:var(--review-bg);text-align:center}
.review .section-title{padding-top:48px}
.review .rule{margin:12px auto 0}
.quote{width:880px;margin:32px auto 0;font-style:italic;font-size:13.5px;line-height:22px;color:var(--muted)}
.quote .qmark{font-family:Georgia,serif;font-style:normal;font-size:34px;color:#8a8a8a;vertical-align:-10px;margin-right:6px}
.reviewer{margin-top:18px;color:var(--blue);font-weight:700;font-size:15px}
.stars{margin-top:8px;display:flex;justify-content:center;gap:4px}
.rv-arrow{position:absolute;top:135px}

/* footer */
.site-footer{height:294px;background:var(--footer-bg);color:#ddd}
.f-col{position:absolute;top:40px}
.f-col h4{font-family:"Cinzel",Georgia,serif;font-weight:400;font-size:18px;color:var(--blue);white-space:nowrap}
.f-col h4 em{font-style:normal;color:var(--green)}
.f-rule{width:40px;height:2px;background:var(--blue);margin-top:6px}
.quick{left:0}
.quick ul{list-style:none;margin-top:16px}
.quick li{font-size:13px;height:31px}
.quick li::before{content:"•";margin-right:6px}
.quick li.current{color:#e2c02a}
.contact{left:195px}
.contact .row{display:flex;gap:10px;font-size:13px;line-height:18px;margin-top:16px}
.contact .row:first-of-type{margin-top:20px}
.mapcol{left:497px}
.map{width:290px;height:176px;margin-top:18px;background:linear-gradient(135deg,#e9eae4,#d9dcd4 60%,#c9cfc6);border:2px solid #fff}
.follow{left:873px;width:167px}
.social{display:flex;gap:10px;margin-top:16px;font-size:13px;flex-wrap:wrap}
.social span{display:flex;align-items:center;gap:6px}
.social i{width:18px;height:18px;border-radius:50%;background:var(--blue);display:inline-block}
.donate{font-size:13px;font-weight:700;margin-top:22px;line-height:17px;color:#fff}
.badges{display:flex;gap:12px;margin-top:12px}
.badge{width:78px;height:38px;background:#fff;border-radius:2px}
.copyright{height:45px;background:var(--footer-deep);color:#ddd;text-align:center;font-size:13px;line-height:45px}
</style>
</head>
<body>

<header class="site-header">
  <div class="wrap">
    <div class="brand">Dr. Mara Z. Kalvoric</div>
    <div class="pill pill-email">
      <svg viewBox="0 0 20 20"><rect x="2" y="4" width="16" height="12" rx="2" fill="none" stroke="#108c12" stroke-width="1.8"/><path d="M2 5l8 6 8-6" fill="none" stroke="#108c12" stroke-width="1.8"/></svg>
      <span><b>Email Us</b> mk@drkalvoric.com</span>
    </div>
    <div class="pill pill-call">
      <svg viewBox="0 0 20 20"><path d="M5 2l3 4-2 2c1 2 3 4 6 6l2-2 4 3-2 3C9 18 2 11 2 4z" fill="none" stroke="#108c12" stroke-width="1.6"/></svg>
      <span>Call Us (949) 555 0148</span>
    </div>
  </div>
</header>

<nav class="main-nav">
  <div class="wrap">
    <ul>
      <li class="active">HOME</li><li class="sep"></li>
      <li>BIO</li><li class="sep"></li>
      <li>MY EXPERTISE</li><li class="sep"></li>
      <li>SESSIONS</li><li class="sep"></li>
      <li>RESOURCES</li><li class="sep"></li>
      <li>CONTACT ME</li>
    </ul>
  </div>
</nav>

<section class="hero" role="img" aria-label="Photograph of a couple talking on a sofa during a counseling session with the therapist in the foreground">
  <div class="hero-caption">
    <h1>I provide individual and marital counseling</h1>
    <span class="btn-start">Get Started</span>
  </div>
  <span class="arrow left"><svg width="12" height="14" viewBox="0 0 12 14"><path d="M9 1L3 7l6 6" fill="none" stroke="#fff" stroke-width="2.5"/></svg></span>
  <span class="arrow right"><svg width="12" height="14" viewBox="0 0 12 14"><path d="M3 1l6 6-6 6" fill="none" stroke="#fff" stroke-width="2.5"/></svg></span>
</section>

<section class="about">
  <div class="wrap">
    <div class="about-main">
      <h2 class="section-title">About <em>Dr. Mara Z. Kalvoric</em></h2>
      <div class="rule"></div>
      <p class="about-text">While I acknowledge the importance of my education, I also appreciate the role my experiences have played in allowing me to relate so well to others. Allow me to share those I feel are most relevant with you.I survived an abusive childhood that my mother and sister unfortunately did not &nbsp;…… <a href="#">Read More</a></p>
      <div class="values">
        <div class="value">
          <div class="value-icon"><svg width="40" height="40" viewBox="0 0 40 40"><path d="M8 34V22a12 12 0 1 1 20 8v4" fill="#108c12"/><rect x="14" y="9" width="14" height="10" rx="5" fill="#fff"/></svg></div>
          <div><h3>My Philosophy</h3><p>Lorem ipsum dolor sit amet,conse ctetuer adipiscing elit,</p></div>
        </div>
        <div class="value">
          <div class="value-icon"><svg width="40" height="40" viewBox="0 0 40 40"><circle cx="20" cy="20" r="14" fill="none" stroke="#108c12" stroke-width="3"/><circle cx="20" cy="20" r="7" fill="none" stroke="#2a7fc1" stroke-width="3"/><path d="M20 20L33 7" stroke="#108c12" stroke-width="3"/></svg></div>
          <div><h3>My Mission</h3><p>Lorem ipsum dolor sit amet,conse ctetuer adipiscing elit,</p></div>
        </div>
      </div>
    </div>
    <aside class="inquiry">
      <h2>QUICK INQUIRY</h2>
      <form>
        <div class="field">Full Name</div>
        <div class="field">Phone Number</div>
        <div class="field">Email<span class="caret"></span></div>
        <div class="field msg">Message</div>
        <span class="btn-submit">SUBMIT</span>
      </form>
    </aside>
  </div>
</section>

<section class="expertise">
  <div class="wrap">
    <div class="exp-col">
      <h2 class="section-title">My <em>Expertise</em></h2>
      <div class="rule"></div>
      <ul class="checklist">
        <li><svg width="16" height="12" viewBox="0 0 16 12"><path d="M1 6l5 5L15 1" fill="none" stroke="#108c12" stroke-width="2.5"/></svg>DATING</li>
        <li><svg width="16" height="12" viewBox="0 0 16 12"><path d="M1 6l5 5L15 1" fill="none" stroke="#108c12" stroke-width="2.5"/></svg>MARRIAGE</li>
        <li><svg width="16" height="12" viewBox="0 0 16 12"><path d="M1 6l5 5L15 1" fill="none" stroke="#108c12" stroke-width="2.5"/></svg>PARENTING &amp; PROFESSIONAL</li>
        <li><svg width="16" height="12" viewBox="0 0 16 12"><path d="M1 6l5 5L15 1" fill="none" stroke="#108c12" stroke-width="2.5"/></svg>RELATIONSHIPS</li>
        <li><svg width="16" height="12" viewBox="0 0 16 12"><path d="M1 6l5 5L15 1" fill="none" stroke="#108c12" stroke-width="2.5"/></svg>DEPRESSION &amp; ANXIETY ISSUES</li>
        <li><svg width="16" height="12" viewBox="0 0 16 12"><path d="M1 6l5 5L15 1" fill="none" stroke="#108c12" stroke-width="2.5"/></svg>PERSONALITY DISORDERS</li>
        <li><svg width="16" height="12" viewBox="0 0 16 12"><path d="M1 6l5 5L15 1" fill="none" stroke="#108c12" stroke-width="2.5"/></svg>DIVORCE MEDIATION</li>
        <li><svg width="16" height="12" viewBox="0 0 16 12"><path d="M1 6l5 5L15 1" fill="none" stroke="#108c12" stroke-width="2.5"/></svg>LIFE MANAGEMENT</li>
      </ul>
    </div>
    <div class="video-col">
      <h2 class="section-title">View <em>Video</em></h2>
      <div class="rule"></div>
    </div>
    <div class="video" role="img" aria-label="Video still of a family counseling session in a living room">
      <svg width="60" height="60" viewBox="0 0 60 60"><circle cx="30" cy="30" r="27" fill="rgba(0,0,0,.25)" stroke="#fff" stroke-width="3"/><path d="M24 18l18 12-18 12z" fill="#fff"/></svg>
    </div>
  </div>
</section>

<section class="sessions">
  <div class="wrap">
    <div class="sessions-head">
      <h2 class="section-title">My Sessions</h2>
      <div class="rule"></div>
    </div>
    <ul class="session-list">
      <li><svg width="18" height="16" viewBox="0 0 18 16"><path d="M1 8l5 6L17 1" fill="none" stroke="#2a7fc1" stroke-width="2.5"/></svg><span>Individual sessions are 50 minutes in length</span></li>
      <li><svg width="18" height="16" viewBox="0 0 18 16"><path d="M1 8l5 6L17 1" fill="none" stroke="#2a7fc1" stroke-width="2.5"/></svg><span>Marriage sessions are typically 50 to 75 minutes in length</span></li>
      <li><svg width="18" height="16" viewBox="0 0 18 16"><path d="M1 8l5 6L17 1" fill="none" stroke="#2a7fc1" stroke-width="2.5"/></svg><span>Family sessions are 60 to 75 minutes in length</span></li>
      <li><svg width="18" height="16" viewBox="0 0 18 16"><path d="M1 8l5 6L17 1" fill="none" stroke="#2a7fc1" stroke-width="2.5"/></svg><span>Divorce Mediation sessions are primarily conducted with individual sessions for each spouse with meetings as a couple kept to a minimum</span></li>
      <li><svg width="18" height="16" viewBox="0 0 18 16"><path d="M1 8l5 6L17 1" fill="none" stroke="#2a7fc1" stroke-width="2.5"/></svg><span>Custody Evaluation sessions are usually initiated by each parties attorneys or the presiding judge</span></li>
      <li><svg width="18" height="16" viewBox="0 0 18 16"><path d="M1 8l5 6L17 1" fill="none" stroke="#2a7fc1" stroke-width="2.5"/></svg><span>Testing sessions vary in length dependent upon the nature of the psychological assessment needed</span></li>
    </ul>
    <div class="radio">
      <h2 class="section-title">Radio <em>Conversations</em></h2>
      <div class="rule"></div>
    </div>
    <div class="radio-art" role="img" aria-label="Promotional poster for the Silver Cedar Tunes radio show, airing Sundays at 4pm PST / 7pm EST"></div>
  </div>
</section>

<section class="review">
  <div class="wrap">
    <h2 class="section-title">Patient Review</h2>
    <div class="rule"></div>
    <p class="quote"><span class="qmark">“</span>Lorem ipsum dolor sit amet, consectetuer adipiscing elit, sed diam nonummy nibh euismod tincidunt ut laoreet dolore magna aliquam erat volutpat. Ut wisi enim ad minim veniam, quis nostrud exerci tation ullamcorper suscipit lobortis nisl ut aliquip ex ea commodo consequat. Duis autem vel eum iriure.</p>
    <div class="reviewer">-Sam Dorell</div>
    <div class="stars">
      <svg width="18" height="18" viewBox="0 0 20 20"><path d="M10 1l2.7 6 6.3.6-4.8 4.3 1.4 6.3L10 15l-5.6 3.2 1.4-6.3L1 7.6 7.3 7z" fill="#108c12"/></svg>
      <svg width="18" height="18" viewBox="0 0 20 20"><path d="M10 1l2.7 6 6.3.6-4.8 4.3 1.4 6.3L10 15l-5.6 3.2 1.4-6.3L1 7.6 7.3 7z" fill="#108c12"/></svg>
      <svg width="18" height="18" viewBox="0 0 20 20"><path d="M10 1l2.7 6 6.3.6-4.8 4.3 1.4 6.3L10 15l-5.6 3.2 1.4-6.3L1 7.6 7.3 7z" fill="#108c12"/></svg>
      <svg width="18" height="18" viewBox="0 0 20 20"><path d="M10 1l2.7 6 6.3.6-4.8 4.3 1.4 6.3L10 15l-5.6 3.2 1.4-6.3L1 7.6 7.3 7z" fill="#108c12"/></svg>
      <svg width="18" height="18" viewBox="0 0 20 20"><path d="M10 1l2.7 6 6.3.6-4.8 4.3 1.4 6.3L10 15l-5.6 3.2 1.4-6.3L1 7.6 7.3 7z" fill="#108c12"/></svg>
    </div>
    <svg class="rv-arrow" style="left:-4px" width="14" height="22" viewBox="0 0 14 22"><path d="M12 2L3 11l9 9" fill="none" stroke="#aaa" stroke-width="2"/></svg>
    <svg class="rv-arrow" style="right:-4px" width="14" height="22" viewBox="0 0 14 22"><path d="M2 2l9 9-9 9" fill="none" stroke="#aaa" stroke-width="2"/></svg>
  </div>
</section>

<footer class="site-footer">
  <div class="wrap">
    <div class="f-col quick">
      <h4>Quick <em>Links</em></h4><div class="f-rule"></div>
      <ul>
        <li class="current">Home</li><li>Sessions</li><li>My Expertise</li><li>Resources</li><li>Bio</li><li>Contact Us</li>
      </ul>
    </div>
    <div class="f-col contact">
      <h4>Contact <em>Details</em></h4><div class="f-rule"></div>
      <div class="row"><svg width="14" height="18" viewBox="0 0 14 18"><path d="M7 17S1 10 1 6.5a6 6 0 0 1 12 0C13 10 7 17 7 17z" fill="#ddd"/><circle cx="7" cy="6.5" r="2.3" fill="#262626"/></svg><span><b>Dr. Mara Z. Kalvoric</b><br>418 Larkspur Lane #120<br>Harbor Cove, CA, 92655</span></div>
      <div class="row"><svg width="14" height="14" viewBox="0 0 20 20"><path d="M5 2l3 4-2 2c1 2 3 4 6 6l2-2 4 3-2 3C9 18 2 11 2 4z" fill="#ddd"/></svg><span>(949) 555 0148</span></div>
      <div class="row"><svg width="12" height="16" viewBox="0 0 12 16"><rect x="1" y="1" width="10" height="14" rx="2" fill="none" stroke="#ddd" stroke-width="1.6"/></svg><span>(949) 555 0148</span></div>
      <div class="row"><svg width="14" height="12" viewBox="0 0 20 16"><rect x="1" y="1" width="18" height="14" fill="#ddd"/><path d="M1 2l9 7 9-7" fill="none" stroke="#262626" stroke-width="1.6"/></svg><span>mk@drkalvoric.com</span></div>
    </div>
    <div class="f-col mapcol">
      <h4>Location <em>Map</em></h4><div class="f-rule"></div>
      <div class="map" role="img" aria-label="Street map showing the office location"></div>
    </div>
    <div class="f-col follow">
      <h4>Follow <em>Us</em></h4><div class="f-rule"></div>
      <div class="social"><span><i></i>Friendora</span><span><i></i>Chirpline</span></div>
      <p class="donate">A portion of all revenue<br>is donated to</p>
      <div class="badges"><span class="badge"></span><span class="badge"></span></div>
    </div>
  </div>
</footer>
<div class="copyright">Copyright © 2016 Dr. Mara Z. Kalvoric. All Rights Reserved</div>

</body>
</html>
```